RM Installations Web Site Design

Need a basic site to show clients a little about what we do. We are a custom audio video company in the high-end residential market. Need a few basic but professional pages to show past projects and products we sell. No e-commerce. Should include my new logo from MarkBazaar.

Industry/Entity Type

Residential

Number of Pages Required

2 page

Font styles to use
Serif
Sans Serif

Colors
f78f20

Requirements
Must have
• Company Logo, Send feedback page
Nice to have
• I have no ideas about design, but I do know what I like and dislike when I see it.

```html
<!DOCTYPE html>
<html lang="en">
<head>
<meta charset="utf-8">
<title>RM Installations – Custom Audio Video</title>
<link href="https://fonts.googleapis.com/css2?family=Lato:wght@400;700&display=swap" rel="stylesheet">
<style>
:root{
  --orange:#f78f20;
  --ink:#2e2e2e;
  --text:#444;
  --nav:#1f1f1f;
  --grey-band:#ebebeb;
  --dark-band:#5e5e5e;
  --footer:#2a2a2a;
  --footer-base:#121212;
  --line:#9a9a9a;
}
*{box-sizing:border-box;margin:0;padding:0}
html,body{width:674px;height:1200px;overflow:hidden;background:#fff}
body{position:relative;font-family:'Lato',sans-serif;color:var(--text)}
.abs{position:absolute}
.center{left:0;width:674px;text-align:center}

/* header */
.nav-bar{top:30px;left:0;width:674px;height:27px;background:var(--nav)}
.brand{top:0;left:70px;width:168px;height:53px;background:#fff;display:flex;align-items:center;gap:8px;padding-left:10px}
.brand-mark{width:22px;height:22px;background:var(--orange)}
.brand-name{font-size:15px;font-weight:700;color:var(--ink);line-height:1}
.feedback-btn{top:5px;left:423px;width:50px;height:16px;border:1px solid var(--orange);border-radius:2px;font-size:6.5px;font-weight:700;color:var(--ink);display:flex;align-items:center;justify-content:center}
.call{top:3px;left:504px;display:flex;gap:6px;align-items:center}
.call-label{font-size:7.5px;letter-spacing:1.2px;color:var(--ink)}
.call-number{font-size:11px;font-weight:700;color:var(--ink)}
.nav{top:30px;left:251px;height:27px;display:flex}
.nav a{display:flex;align-items:center;padding:0 10px;height:27px;font-size:8.5px;font-weight:700;color:#fff;text-decoration:none;border-right:1px solid #444}
.nav a.active{background:var(--orange)}

/* hero */
.hero{top:57px;left:0;width:674px;height:238px;background:linear-gradient(180deg,#4a3826 0%,#6b5236 45%,#3a2c1f 100%)}
.hero-caption{top:260px;left:0;width:674px;height:35px;background:rgba(40,40,40,.75);color:#eee;font-size:24px;display:flex;align-items:center;justify-content:center}

/* headings */
.section-title{font-size:24px;color:var(--ink);letter-spacing:.3px}
.section-title .hl{color:var(--orange)}
.divider{display:flex;align-items:center;justify-content:center;gap:14px}
.divider span{display:block;width:82px;height:1px;background:var(--line)}
.divider i{display:block;width:9px;height:9px;background:var(--orange);transform:rotate(45deg)}

.welcome-kicker{top:318px;font-size:17px;color:var(--orange)}
.welcome-title{top:336px;font-size:24px;color:var(--ink)}
.welcome-copy{top:385px;left:137px;width:400px;font-size:7.6px;line-height:13.5px;text-align:center;color:var(--ink)}
.read-more{top:435px;left:311px;width:52px;height:15px;border:1px solid var(--orange);border-radius:2px;font-size:6.3px;font-weight:700;display:flex;align-items:center;justify-content:center;color:var(--ink)}

/* services */
.services{top:477px;left:0;width:674px;height:221px;background:var(--grey-band)}
.band-shadow{left:70px;width:534px;height:10px;border-radius:50%;background:radial-gradient(ellipse at center,rgba(0,0,0,.25),rgba(0,0,0,0) 70%)}
.service{top:553px;width:100px;text-align:center}
.service-icon{width:64px;height:64px;border-radius:50%;background:#111;border:3px solid #fff;margin:0 auto;box-shadow:0 1px 3px rgba(0,0,0,.2)}
.service-icon.featured{background:var(--orange)}
.service h3{margin-top:12px;font-size:9px;line-height:11px;font-weight:700;color:var(--ink)}
.service p{margin-top:7px;font-size:7px;line-height:11px;color:var(--text)}
.service-sep{top:565px;width:1px;height:120px;background:#dcdcdc}
.arrow{font-size:0}

/* projects */
.projects{top:720px;left:0;width:674px;height:200px;background:var(--dark-band)}
.projects .section-title{color:#d6d6d6}
.thumb{top:803px;width:123px;height:80px;border:3px solid #fff;box-shadow:0 3px 5px rgba(0,0,0,.35)}

/* contact */
.field{border:1px solid #555;border-radius:2px;font-size:7px;color:#aaa;padding:3px 12px;background:#fff}
.submit{top:1052px;left:513px;width:51px;height:16px;border:1px solid var(--orange);border-radius:2px;font-size:8px;font-weight:700;color:var(--ink);display:flex;align-items:center;justify-content:center}

/* footer */
.footer{top:1094px;left:0;width:674px;height:79px;background:var(--footer)}
.footer-links{top:1103px;left:140px;display:flex;font-size:8px;color:#ddd}
.footer-links a{padding:0 13px;border-left:1px solid #aaa;color:#ddd;text-decoration:none;line-height:11px}
.footer-links a:last-child{border-right:1px solid #aaa}
.footer-links a.active{color:var(--orange)}
.footer-info{font-size:7.2px;line-height:9px;color:#eee;display:flex;gap:6px}
.socials{top:1144px;left:376px;display:flex;gap:7px}
.socials span{width:13px;height:13px;background:#e6e6e6}
.socials span:first-child{background:var(--orange)}
.footer-brand{top:1128px;left:480px;display:flex;align-items:center;gap:7px}
.footer-brand i{width:30px;height:30px;background:#888}
.footer-brand b{font-size:12px;font-weight:700;color:#bbb}
.base{top:1173px;left:0;width:674px;height:27px;background:var(--footer-base);font-size:7.5px;color:#ddd;display:flex;align-items:center;justify-content:center}
</style>
</head>
<body>

<header>
  <div class="abs nav-bar"></div>
  <div class="abs brand"><span class="brand-mark"></span><span class="brand-name">RM INSTALLATIONS</span></div>
  <div class="abs feedback-btn">FEEDBACK</div>
  <div class="abs call">
    <svg width="20" height="20" viewBox="0 0 20 20"><circle cx="10" cy="10" r="9" fill="none" stroke="#f78f20" stroke-width="1.4"/><path d="M7 5.5l2 2.2-1 1.2c.6 1.3 1.6 2.3 2.9 2.9l1.2-1 2.2 2-1.3 1.6C9.8 14.2 5.8 10.2 5.6 7z" fill="#f78f20"/></svg>
    <div><div class="call-label">CALL US TODAY</div><div class="call-number">555-014-2290</div></div>
  </div>
  <nav class="abs nav">
    <a class="active" href="#">HOME</a><a href="#">ABOUT US</a><a href="#">Product &amp; Services</a><a href="#">Past Projects</a><a href="#">CONTACT US</a>
  </nav>
</header>

<div class="abs hero" role="img" aria-label="Home theater room with sofas facing a large projection screen"></div>
<div class="abs hero-caption">We Are Custom Audio Video Company</div>

<section>
  <div class="abs center welcome-kicker">WELCOME TO</div>
  <div class="abs center welcome-title">RM INSTALLATIONS</div>
  <div class="abs center divider" style="top:364px"><span></span><i></i><span></span></div>
  <p class="abs welcome-copy">Lorem Ipsum Dolor Sit Amet, Consectetur Adipiscing Elit. Aenean Sodales Diam Quis Velit Pellentesque Vehicula. Donec Luctus Justo Aliquet Est Volutpat, Sedtincidunt Odio Pretium. Sed Id Est Ultrici Rutrum Arcu Pretium, Porttitor Enim. Integer Quis Luctus Ligula. Donec Id Scelerisque Lorem.</p>
  <div class="abs read-more">READ MORE »</div>
</section>

<section>
  <div class="abs services"></div>
  <div class="abs center section-title" style="top:497px"><span class="hl">OUR</span> SERVICES</div>
  <div class="abs center divider" style="top:529px"><span style="width:36px"></span><i></i><span style="width:36px"></span></div>

  <svg class="abs" style="top:609px;left:29px" width="12" height="18" viewBox="0 0 12 18"><path d="M10 1L2 9l8 8" fill="none" stroke="#555" stroke-width="1.6"/></svg>
  <svg class="abs" style="top:609px;left:633px" width="12" height="18" viewBox="0 0 12 18"><path d="M2 1l8 8-8 8" fill="none" stroke="#555" stroke-width="1.6"/></svg>

  <div class="abs service-sep" style="left:171px"></div>
  <div class="abs service-sep" style="left:281px"></div>
  <div class="abs service-sep" style="left:391px"></div>
  <div class="abs service-sep" style="left:501px"></div>

  <div class="abs service" style="left:68px"><div class="service-icon featured" role="img" aria-label="Distributed video icon"></div><h3>Distributed<br>Video</h3><p>Lorem ipsum dolor si amet consectetur adipiscing elit Etiam feugiat urna leo</p></div>
  <div class="abs service" style="left:176px"><div class="service-icon" role="img" aria-label="Media rooms icon"></div><h3>Media<br>Rooms</h3><p>Lorem ipsum dolor si amet consectetur adipiscing elit Etiam feugiat urna leo</p></div>
  <div class="abs service" style="left:286px"><div class="service-icon" role="img" aria-label="Residential cinemas icon"></div><h3>Residential<br>Cinemas</h3><p>Lorem ipsum dolor si amet consectetur adipiscing elit Etiam feugiat urna leo</p></div>
  <div class="abs service" style="left:396px"><div class="service-icon" role="img" aria-label="Whole-house control icon"></div><h3>Whole-House<br>Control Systems</h3><p>Lorem ipsum dolor si amet consectetur adipiscing elit Etiam feugiat urna leo</p></div>
  <div class="abs service" style="left:508px"><div class="service-icon" role="img" aria-label="Automated lighting icon"></div><h3>Automated<br>Lighting Control</h3><p>Lorem ipsum dolor si amet consectetur adipiscing elit Etiam feugiat urna leo</p></div>
  <div class="abs band-shadow" style="top:697px"></div>
</section>

<section>
  <div class="abs projects"></div>
  <div class="abs center section-title" style="top:740px"><span class="hl">PAST</span> PROJECTS</div>
  <div class="abs center divider" style="top:772px"><span style="width:58px;background:#bbb"></span><i></i><span style="width:58px;background:#bbb"></span></div>

  <svg class="abs" style="top:834px;left:49px" width="10" height="16" viewBox="0 0 10 16"><path d="M8 1L2 8l6 7" fill="none" stroke="#fff" stroke-width="1.6"/></svg>
  <svg class="abs" style="top:834px;left:616px" width="10" height="16" viewBox="0 0 10 16"><path d="M2 1l6 7-6 7" fill="none" stroke="#fff" stroke-width="1.6"/></svg>

  <div class="abs thumb" style="left:74px;background:linear-gradient(180deg,#3b4a6b,#6b3a2a)" role="img" aria-label="Sports bar with wall of screens"></div>
  <div class="abs thumb" style="left:208px;background:linear-gradient(180deg,#8a2b1f,#3a1f19)" role="img" aria-label="Red private cinema with recliners"></div>
  <div class="abs thumb" style="left:342px;background:linear-gradient(135deg,#e6e6e6,#b7b7b7 60%,#c94a3a)" role="img" aria-label="Wall-mounted control touch panel in use"></div>
  <div class="abs thumb" style="left:477px;background:linear-gradient(180deg,#1a1a1a,#4a2a25)" role="img" aria-label="Touch screen tablet showing a media room"></div>
  <div class="abs band-shadow" style="top:918px"></div>
</section>

<section>
  <div class="abs center section-title" style="top:940px"><span class="hl">QUICK</span> CONTACT</div>
  <div class="abs center divider" style="top:972px"><span style="width:58px"></span><i></i><span style="width:58px"></span></div>
  <div class="abs field" style="top:999px;left:74px;width:169px;height:18px">Name</div>
  <div class="abs field" style="top:999px;left:252px;width:169px;height:18px">Mob</div>
  <div class="abs field" style="top:999px;left:430px;width:170px;height:18px">Email</div>
  <div class="abs field" style="top:1024px;left:74px;width:432px;height:44px">Message</div>
  <div class="abs submit">SUBMIT</div>
</section>

<footer>
  <div class="abs footer"></div>
  <div class="abs footer-links"><a class="active" href="#">Home</a><a href="#">About Us</a><a href="#">Product &amp; Services</a><a href="#">Past Projects</a><a href="#">Feedback</a><a href="#">Contact Us</a></div>
  <div class="abs footer-info" style="top:1131px;left:73px">
    <svg width="7" height="9" viewBox="0 0 7 9"><path d="M3.5 0A3 3 0 0 0 .5 3c0 2.2 3 6 3 6s3-3.8 3-6a3 3 0 0 0-3-3z" fill="#fff"/><circle cx="3.5" cy="3" r="1.1" fill="#2a2a2a"/></svg>
    <div>Lorem Ipsum,<br>Dolor sit amet consectetuer,<br>Adipiscing - 12345</div>
  </div>
  <div class="abs footer-info" style="top:1131px;left:211px">
    <svg width="9" height="9" viewBox="0 0 9 9"><path d="M1.5 .5l2 2-1 1.2c.6 1.2 1.5 2 2.8 2.8l1.2-1 2 2-1.3 1.3C3.8 8.3.7 5.2.3 1.8z" fill="#fff"/></svg>
    <div>Phone: 555 014 2290</div>
  </div>
  <div class="abs footer-info" style="top:1148px;left:211px">
    <svg width="10" height="8" viewBox="0 0 10 8"><rect x=".5" y=".5" width="9" height="7" fill="none" stroke="#fff"/><path d="M.5.5L5 4.5 9.5.5" fill="none" stroke="#fff"/></svg>
    <div>hello@rminstallations.example</div>
  </div>
  <div class="abs socials"><span></span><span></span><span></span><span></span></div>
  <div class="abs footer-brand"><i></i><b>RM INSTALLATIONS</b></div>
  <div class="abs base">© 2015 RMInstallationsAudioVideo &nbsp;|&nbsp; All rights reserved</div>
</footer>

</body>
</html>
```